Research and Innovation programme/projects in WOOD based industries

1.Pramenova s.r.o. (offical registered brand name of our company)
-Managing technology development projects
-International cooperation and development European projects
Our company was founded in 2008 and started to work as a counsilary company operating in the section of european funds administrated by Czech republic. Nowadays we are specializing on projects in the sphere of science and research co-financed by EU.Since 6.6.2013 we are registered under European comission for a purpose of broad support of transnational projects.

Target Market(s)

We are primarily focused on european companies, which stand behind the latest research and innovation of sawing, planing, glulam and logging technologies based on wooden materials.

Coding

Coded - Design and coding required

Number of Pages Required

5+ page

Font styles to use
Serif

Colors
cadf82
abd037
9bcb3c
fee18a
ffcf3e
ffc214

Requirements
Must have
• The web will exist in three possible languages in czech, english and deutsch.
• First page : introduction of a company
• Second page : Area of expertise
• Third page: servicies our company provides
• Fourth page: Our partners
• Fifth page: Conditions of our servicies
• Sixth page: Succesful projects
• - we would also love if we had possibility to add videos about our successful projects
• Seventh: Our team
• We are serious company in the sphere of funds and counsilary servicies, that is why we would love to have web design as representative as possible
• Take on mind that that we are specializing on development management, try to apply that on your design
• In the section of contacts, we would love to have photos of our team,
• This is our current site: http://www.pramenova-example.eu/cz/partneri.html
• This is how our concurency sites are lookin. Take these designs as an slight inspiration.
• http://www.lumatrava-example.sk/en/
• https://www2.brenvick-example.com/global/en.html
Nice to have
• Visible logo on the front page for the visitor.
• As a inspiration we provided link for our current web design, but we dont want to copy the current style, just look at the logo and the pages that exists on current web.
• !!!!!!We also uploaded file, where we explain how our cooperation with partner works. Especially in the part 2. section of service. Take that as an ispiration too, or use that to understand, what our company do.
Should not have
• We are serious company in the sphere of funds and counsilary servicies, that is why we would love to have web design representative as possible

```html
<!DOCTYPE html>
<html lang="en">
<head>
<meta charset="utf-8">
<title>Pramenova s.r.o. – Beratungsfirma</title>
<link href="https://fonts.googleapis.com/css2?family=Raleway:wght@500;600;700;800&family=Lato:wght@400;700&display=swap" rel="stylesheet">
<style>
:root{
  --orange:#fb9410;
  --orange-deep:#f58a00;
  --yellow:#fddf87;
  --ink:#1d1d1d;
  --text:#4a4a4a;
  --muted:#8a8a8a;
  --grey-band:#ecebea;
  --white:#ffffff;
  --footer:#1c1c1c;
  --footer-alt:#151413;
}
*{box-sizing:border-box;margin:0;padding:0}
html,body{width:1200px;height:5268px;overflow:hidden}
body{font-family:"Lato",sans-serif;color:var(--text);background:var(--white);position:relative}
.abs{position:absolute}
section,header,footer{position:absolute;left:0;width:1200px;overflow:hidden}
.h-font{font-family:"Raleway",sans-serif}
.btn{position:absolute;display:flex;align-items:center;justify-content:center;background:var(--orange);color:var(--white);font-family:"Raleway",sans-serif;font-weight:700;font-size:14px;letter-spacing:.3px}
.label{position:absolute;font-family:"Raleway",sans-serif;font-weight:700;color:var(--orange);font-size:15px;text-transform:uppercase}
.title{position:absolute;font-family:"Raleway",sans-serif;font-weight:800;color:var(--ink);font-size:34px;text-transform:uppercase}
.title .accent{color:var(--orange)}
.center{left:0;width:1200px;text-align:center}
.para{position:absolute;font-size:13px;line-height:28px;color:var(--text);text-align:justify}
.ph{position:absolute}

/* hero */
.hero{top:0;height:671px;background:linear-gradient(180deg,#3d7fc0 0%,#7fb0d8 30%,#c99a5e 58%,#8a5a2c 80%,#3f3020 100%)}
.hero-shade{position:absolute;inset:0;background:linear-gradient(180deg,rgba(0,0,0,.25),rgba(0,0,0,.05) 40%,rgba(0,0,0,.2))}
.lang{left:110px;top:20px;color:var(--orange);font-size:14px;font-weight:700}
.brand{left:110px;top:62px;display:flex;align-items:center;gap:12px}
.brand-mark{width:46px;height:36px;background:var(--orange)}
.brand-name{font-family:"Raleway",sans-serif;font-weight:700;color:var(--white);font-size:15px;line-height:20px}
.brand-name span{display:block;color:var(--orange);font-weight:600}
.auth-out{left:867px;top:12px;width:92px;height:41px;border:2px solid var(--orange);background:transparent;color:var(--orange)}
.auth-in{left:969px;top:12px;width:111px;height:41px}
.nav a{position:absolute;top:68px;color:var(--white);font-family:"Raleway",sans-serif;font-weight:700;font-size:14px;text-decoration:none}
.nav .active{left:417px;top:57px;width:92px;height:41px;border:2px solid var(--orange);color:var(--orange);display:flex;align-items:center;justify-content:center}
.hero-title{top:280px;font-family:"Raleway",sans-serif;font-weight:800;color:var(--white);font-size:56px;letter-spacing:1px}
.hero-btn{left:546px;top:374px;width:143px;height:41px}
.dots{left:576px;top:578px;display:flex;gap:6px}
.dots i{width:12px;height:12px;border-radius:50%;border:2px solid var(--white);display:block}
.dots i.on{background:var(--white)}

/* welcome */
.welcome{top:671px;height:503px;background:var(--white)}
.frame{left:654px;top:82px;width:393px;height:302px;border:3px solid var(--orange)}

/* expertise */
.expertise{top:1174px;height:589px;background:linear-gradient(90deg,#e8e6e3,#f1f0ee 50%,#e6e4e1)}
.ph-label{display:flex;align-items:center;justify-content:center;color:var(--white);font-family:"Raleway",sans-serif;font-weight:700;font-size:14px}
.list{position:absolute;left:628px;font-size:13px;color:var(--text)}

/* services */
.services{top:1763px;height:885px;background:var(--white)}
.grid{position:absolute;left:112px;top:174px;width:976px;height:533px;display:grid;grid-template-columns:repeat(3,1fr);grid-template-rows:repeat(2,1fr);gap:2px}
.cell{display:flex;flex-direction:column;align-items:center;justify-content:flex-end;padding-bottom:34px;text-align:center;font-family:"Raleway",sans-serif;font-weight:700;font-size:14px;line-height:28px;text-transform:uppercase}
.cell svg{margin-bottom:28px}
.cell.light{background:var(--yellow);color:#3a2a10}
.cell.light svg{stroke:var(--orange-deep)}
.cell.dark{background:var(--orange);color:var(--white)}
.cell.dark svg{stroke:var(--white)}

/* partners */
.partners{top:2648px;height:368px;background:linear-gradient(90deg,#e7e5e2,#efeeec 50%,#e5e3e0)}
.partner{position:absolute;top:190px;display:flex;align-items:center;gap:12px;font-family:"Raleway",sans-serif;font-weight:700;color:#8c8c8c;font-size:28px;letter-spacing:1px}
.partner i{display:block;width:34px;height:34px;border-radius:50%;background:#9a9a9a}

/* conditions */
.conditions{top:3016px;height:644px;background:var(--white)}
.cond-item{position:absolute;left:569px;width:520px;font-size:14px;line-height:31px;color:var(--text);padding-left:47px}
.cond-item svg{position:absolute;left:0;top:4px}

/* projects */
.projects{top:3660px;height:665px;background:linear-gradient(90deg,#e7e5e2,#f0efed 50%,#e6e4e1)}
.arrow{position:absolute;top:353px;width:36px;height:36px;border-radius:50%;border:3px solid #777;display:flex;align-items:center;justify-content:center}
.play{position:absolute;width:66px;height:66px;border-radius:50%;background:var(--orange);display:flex;align-items:center;justify-content:center}
.caption{position:absolute;width:415px;text-align:center;font-family:"Raleway",sans-serif;font-weight:700;font-size:21px;line-height:31px;color:var(--ink)}

/* team */
.team{top:4325px;height:548px;background:var(--white)}
.photo{position:absolute;top:190px;height:195px;border:1px solid #ddd;background:linear-gradient(180deg,#c9c2b8,#8e8478)}
.namebar{position:absolute;top:419px;height:43px}

/* footer */
.site-footer{top:4873px;height:395px;background:var(--footer)}
.footer-alt{position:absolute;left:599px;top:0;width:601px;height:395px;background:linear-gradient(135deg,#211f1d,#141312 60%,#2a2622)}
.f-head{position:absolute;font-family:"Raleway",sans-serif;font-weight:700;color:var(--white);font-size:17px;text-transform:uppercase}
.f-text{position:absolute;color:#d8d8d8;font-size:13px;line-height:28px}
.f-nav{position:absolute;left:425px;top:152px;list-style:none;color:#d8d8d8;font-size:13px;line-height:28px}
.f-nav li::before{content:"»";color:var(--white);margin-right:10px}
.input{position:absolute;left:699px;top:213px;width:289px;height:41px;background:var(--white);color:#999;font-size:12px;display:flex;align-items:center;padding-left:14px;gap:8px}
.rule{position:absolute;top:332px;height:1px;background:#444}
.social{position:absolute;top:338px;width:44px;height:44px;border-radius:50%;background:#3a3a3a}
.social.on{background:var(--orange)}
</style>
</head>
<body>

<header class="hero">
  <div class="hero-shade" role="img" aria-label="Timber house frame under construction against a blue sky"></div>
  <div class="abs lang">ENG ⌄</div>
  <div class="abs brand"><div class="brand-mark"></div><div class="brand-name">PRAMENOVÁ S.R.O.<span>Beratungsfirma</span></div></div>
  <div class="btn auth-out">LOG IN</div>
  <div class="btn auth-in">REGISTER</div>
  <nav class="nav">
    <a class="active">Home</a>
    <a style="left:530px">Services</a>
    <a style="left:620px">Our Projects</a>
    <a style="left:742px">Partners</a>
    <a style="left:834px">Business Conditions</a>
    <a style="left:1018px">Contacts</a>
  </nav>
  <div class="abs center hero-title">PRAMENOVA</div>
  <div class="btn hero-btn">GET STARTED</div>
  <div class="abs dots"><i></i><i class="on"></i><i></i></div>
</header>

<section class="welcome">
  <div class="label" style="left:110px;top:74px">Welcome</div>
  <div class="title" style="left:110px;top:101px;font-size:33px">Pramenova</div>
  <p class="para" style="left:112px;top:142px;width:465px">On the other hand, we denounce with righteous indignation and dislike men who are so beguiled and demoralized by the charms of pleasure of the moment, so blinded by desire, that they cannot foresee the pain and trouble that are bound to ensue; and equal blame belongs to those who fail in their duty through weakness of will, which is the same as saying through shrinking from toil and pain. These cases are perfectly simple and easy to distinguish.</p>
  <div class="btn" style="left:112px;top:362px;width:146px;height:45px">READ MORE ➜</div>
  <div class="abs frame"></div>
  <div class="ph" role="img" aria-label="Worker stacking planed timber boards in a sawmill" style="left:675px;top:102px;width:388px;height:301px;background:linear-gradient(160deg,#7d8a92,#c7b08a 55%,#e2c79b)"></div>
</section>

<section class="expertise">
  <div class="ph" role="img" aria-label="Glulam timber beams" style="left:110px;top:57px;width:246px;height:221px;background:linear-gradient(135deg,#3a2a1a,#c89a5a 55%,#e8c88f)"></div>
  <div class="ph" role="img" aria-label="Wood processing hall interior" style="left:110px;top:278px;width:246px;height:249px;background:linear-gradient(180deg,#9aa3a8,#c9c4bc 50%,#b8443a)"></div>
  <div class="ph ph-label" role="img" aria-label="Timber frame house at dusk" style="left:292px;top:184px;width:244px;height:221px;background:linear-gradient(180deg,#223048,#3e4656 60%,#5a4a38)">PERSPICIATIS</div>
  <div class="title" style="left:626px;top:110px;font-size:32px"><span class="accent">Area</span> of Expertise</div>
  <p class="para" style="left:626px;top:152px;width:454px">On the other hand, we denounce with righteous indignation and dislike men who are so beguiled and demoralized by the charms of pleasure of the moment, so blinded by desire, that they cannot foresee the pain and trouble that are bound to ensue; and equal blame belongs to those who fail in their duty...</p>
  <div class="list" style="top:310px">1. Perspiciatis</div>
  <div class="list" style="top:349px">2. Perspiciatis</div>
  <div class="list" style="top:388px">3. Perspiciatis</div>
  <div class="btn" style="left:628px;top:427px;width:251px;height:45px">VIEW MORE DETAILS</div>
</section>

<section class="services">
  <div class="label center" style="top:87px">Services</div>
  <div class="title center" style="top:108px">Our Company Provides</div>
  <div class="grid">
    <div class="cell light"><svg width="110" height="120" viewBox="0 0 110 120" fill="none" stroke-width="3"><path d="M20 8h50l20 20v84H20z"/><path d="M70 8v20h20"/><path d="M40 50l40 40M80 50L40 90"/></svg>Project Coordination</div>
    <div class="cell dark"><svg width="110" height="120" viewBox="0 0 110 120" fill="none" stroke-width="3"><path d="M10 55L55 15l45 40"/><path d="M22 48v62h66V48"/><circle cx="55" cy="78" r="18"/><path d="M48 78l6 6 10-12"/></svg>Project Financing</div>
    <div class="cell light"><svg width="110" height="120" viewBox="0 0 110 120" fill="none" stroke-width="3"><circle cx="55" cy="62" r="26"/><path d="M29 62h52M55 36c-12 14-12 38 0 52M55 36c12 14 12 38 0 52"/><rect x="45" y="8" width="20" height="14"/><path d="M45 100h20v12H45z"/></svg>Technology and Foreign<br>Trade Projects</div>
    <div class="cell dark"><svg width="150" height="120" viewBox="0 0 150 120" fill="none" stroke-width="3"><rect x="20" y="10" width="50" height="36"/><path d="M45 46v12M10 60h130M20 60v52M130 60v52M90 60v52h40M90 84h40"/></svg>Projects in the Framework of<br>International Cooperation</div>
    <div class="cell light"><svg width="110" height="120" viewBox="0 0 110 120" fill="none" stroke-width="3"><path d="M15 50L55 12l40 38"/><path d="M25 45v45h60V45"/><rect x="45" y="58" width="20" height="32"/><path d="M55 90v24M55 104l-14-8M55 104l14-8"/></svg>EU Projects</div>
    <div class="cell dark"><svg width="110" height="120" viewBox="0 0 110 120" fill="none" stroke-width="3"><circle cx="55" cy="60" r="36"/><circle cx="55" cy="60" r="22"/><path d="M55 14v10M55 96v10M9 60h10M91 60h10M22 27l7 7M81 86l7 7M88 27l-7 7M29 86l-7 7"/></svg>International<br>Development Projects</div>
  </div>
  <div class="btn" style="left:523px;top:752px;width:154px;height:47px">VIEW MORE</div>
</section>

<section class="partners">
  <div class="title center" style="top:68px"><span class="accent">Our</span> Partners</div>
  <div class="partner" style="left:110px"><i></i>NORDVALE INVEST</div>
  <div class="partner" style="left:500px"><i></i>TRAVENTA TRADE</div>
  <div class="partner" style="left:832px;font-size:24px"><i></i>KELMOR CHAMBER</div>
</section>

<section class="conditions">
  <div class="ph" role="img" aria-label="Craftsman inspecting a sheet of veneer in a workshop" style="left:110px;top:111px;width:370px;height:335px;background:linear-gradient(135deg,#4a3a2c,#9a7a58 50%,#d2b38a)"></div>
  <div class="ph" style="left:164px;top:454px;width:67px;height:64px;background:var(--orange)"></div>
  <div class="ph" style="left:262px;top:454px;width:69px;height:64px;background:var(--orange)"></div>
  <div class="ph" style="left:362px;top:454px;width:69px;height:64px;background:var(--orange)"></div>
  <div class="ph" style="left:110px;top:505px;width:70px;height:64px;background:var(--yellow)"></div>
  <div class="ph" style="left:213px;top:518px;width:67px;height:51px;background:var(--yellow)"></div>
  <div class="ph" style="left:311px;top:518px;width:69px;height:51px;background:var(--yellow)"></div>
  <div class="ph" style="left:411px;top:505px;width:69px;height:64px;background:var(--yellow)"></div>
  <div class="label" style="left:569px;top:80px">Conditions of</div>
  <div class="title" style="left:569px;top:104px">Our Services</div>
  <div class="cond-item" style="top:160px"><svg width="24" height="22" viewBox="0 0 24 22"><path d="M2 20c2-9 8-12 14-12V3l7 8-7 8v-5c-6 0-10 2-14 6z" fill="var(--orange)"/></svg>Lorem ipsum dolor sit amet, consectetur adipiscing elit, sed do eiusmod tempor incididunt ut labore et dolore</div>
  <div class="cond-item" style="top:242px"><svg width="24" height="22" viewBox="0 0 24 22"><path d="M2 20c2-9 8-12 14-12V3l7 8-7 8v-5c-6 0-10 2-14 6z" fill="var(--orange)"/></svg>Lorem ipsum dolor sit amet, consectetur adipiscing elit, sed do eiusmod tempor incididunt ut labore et dolore</div>
  <div class="cond-item" style="top:324px"><svg width="24" height="22" viewBox="0 0 24 22"><path d="M2 20c2-9 8-12 14-12V3l7 8-7 8v-5c-6 0-10 2-14 6z" fill="var(--orange)"/></svg>Lorem ipsum dolor sit amet, consectetur adipiscing elit, sed do eiusmod tempor incididunt ut labore et dolore</div>
  <div class="cond-item" style="top:406px"><svg width="24" height="22" viewBox="0 0 24 22"><path d="M2 20c2-9 8-12 14-12V3l7 8-7 8v-5c-6 0-10 2-14 6z" fill="var(--orange)"/></svg>Lorem ipsum dolor sit amet, consectetur adipiscing elit, sed do eiusmod tempor incididunt ut labore et dolore</div>
  <div class="cond-item" style="top:488px"><svg width="24" height="22" viewBox="0 0 24 22"><path d="M2 20c2-9 8-12 14-12V3l7 8-7 8v-5c-6 0-10 2-14 6z" fill="var(--orange)"/></svg>Lorem ipsum dolor sit amet, consectetur adipiscing elit, sed do eiusmod tempor incididunt ut labore et dolore</div>
</section>

<section class="projects">
  <div class="label center" style="top:78px">Successful</div>
  <div class="title center" style="top:100px">Projects</div>
  <div class="ph" role="img" aria-label="Partially visible project photo" style="left:0;top:177px;width:71px;height:263px;background:linear-gradient(160deg,#b9a890,#d8cbb8)"></div>
  <div class="ph" role="img" aria-label="Partially visible project photo" style="left:1124px;top:177px;width:76px;height:263px;background:linear-gradient(160deg,#c0b7aa,#e0d6c6)"></div>
  <div class="ph" role="img" aria-label="Builder working on a timber roof frame under a cloudy sky" style="left:143px;top:177px;width:415px;height:263px;background:linear-gradient(180deg,#4f7fae,#a9c3d9 50%,#b88a52)"></div>
  <div class="ph" role="img" aria-label="Stacks of timber boards inside a production hall" style="left:636px;top:177px;width:415px;height:263px;background:linear-gradient(180deg,#7a8690,#b9aa92 55%,#d9b98a)"></div>
  <div class="play" style="left:318px;top:276px"><svg width="22" height="24" viewBox="0 0 22 24"><path d="M2 2l18 10L2 22z" fill="#fff"/></svg></div>
  <div class="play" style="left:811px;top:276px"><svg width="22" height="24" viewBox="0 0 22 24"><path d="M2 2l18 10L2 22z" fill="#fff"/></svg></div>
  <div class="arrow" style="left:33px"><svg width="16" height="14" viewBox="0 0 16 14"><path d="M8 1L2 7l6 6M2 7h13" stroke="#777" stroke-width="3" fill="none"/></svg></div>
  <div class="arrow" style="left:1129px"><svg width="16" height="14" viewBox="0 0 16 14"><path d="M8 1l6 6-6 6M14 7H1" stroke="#777" stroke-width="3" fill="none"/></svg></div>
  <div class="caption" style="left:143px;top:462px">Lorem ipsum dolor sit amet,<br>consectetur adipiscing</div>
  <div class="caption" style="left:636px;top:462px">Lorem ipsum dolor sit amet,<br>consectetur adipiscing</div>
  <div class="btn" style="left:276px;top:545px;width:147px;height:47px">READ MORE ➜</div>
  <div class="btn" style="left:769px;top:545px;width:147px;height:47px">READ MORE ➜</div>
</section>

<section class="team">
  <div class="label center" style="top:74px">Our Creative</div>
  <div class="title center" style="top:96px">Team</div>
  <div class="photo" role="img" aria-label="Portrait photo of team member Tomáš Hrubec" style="left:207px;width:173px"></div>
  <div class="photo" role="img" aria-label="Portrait photo of team member Lenka Doubravová" style="left:509px;width:180px;background:linear-gradient(180deg,#e9e6e2,#b8a79a)"></div>
  <div class="photo" role="img" aria-label="Portrait photo of team member Marek Sliva" style="left:816px;width:180px;background:linear-gradient(180deg,#a9a7a4,#6f7a86)"></div>
  <div class="btn namebar" style="left:176px;width:233px">Tomáš Hrubec</div>
  <div class="btn namebar" style="left:481px;width:235px">Mgr. Lenka Doubravová</div>
  <div class="btn namebar" style="left:787px;width:233px">Marek Sliva</div>
</section>

<footer class="site-footer">
  <div class="footer-alt" role="img" aria-label="Dark stacked timber texture"></div>
  <div class="abs brand" style="top:86px"><div class="brand-mark"></div><div class="brand-name">PRAMENOVÁ S.R.O.<span style="color:#fff;font-weight:500">Beratungsfirma</span></div></div>
  <svg class="abs" style="left:110px;top:148px" width="12" height="16" viewBox="0 0 12 16"><path d="M6 0a6 6 0 016 6c0 4-6 10-6 10S0 10 0 6a6 6 0 016-6z" fill="var(--orange)"/><circle cx="6" cy="6" r="2" fill="#1c1c1c"/></svg>
  <div class="f-text" style="left:135px;top:142px">Lorem ipsum dolor sit amet,<br>consectetur adipiscing elit</div>
  <svg class="abs" style="left:110px;top:232px" width="14" height="14" viewBox="0 0 14 14"><path d="M3 0l3 3-2 2c1 2 3 4 5 5l2-2 3 3-2 3C6 14 0 8 0 2z" fill="var(--orange)"/></svg>
  <div class="f-text" style="left:135px;top:224px">+1 555 010 0100</div>
  <svg class="abs" style="left:110px;top:284px" width="15" height="11" viewBox="0 0 15 11"><rect width="15" height="11" fill="var(--orange)"/><path d="M0 0l7.5 6L15 0" stroke="#1c1c1c" fill="none"/></svg>
  <div class="f-text" style="left:135px;top:275px">info@pramenova-example.com</div>
  <div class="f-head" style="left:425px;top:90px">Navigation</div>
  <ul class="f-nav"><li>Home</li><li>Services</li><li>Our Projects</li><li>Partners</li><li>Business Conditions</li><li>Contacts</li></ul>
  <div class="f-head" style="left:699px;top:90px">Newsletter</div>
  <div class="f-text" style="left:699px;top:134px">Lorem Ipsum is simply dummy text of the<br>printing and typesetting industry.</div>
  <div class="input"><svg width="13" height="10" viewBox="0 0 13 10"><rect x=".5" y=".5" width="12" height="9" fill="none" stroke="#999"/><path d="M.5.5l6 5 6-5" stroke="#999" fill="none"/></svg>Enter your email address</div>
  <div class="btn" style="left:699px;top:266px;width:105px;height:37px;font-size:12px">SUBSCRIBE</div>
  <div class="rule" style="left:110px;width:434px"></div>
  <div class="rule" style="left:699px;width:303px"></div>
  <div class="f-text" style="left:110px;top:346px">© Copyrights 2019 Pramenova | All Rights Reserved</div>
  <div class="social" style="left:702px" aria-label="Social link"></div>
  <div class="social on" style="left:749px" aria-label="Social link"></div>
  <div class="social" style="left:796px" aria-label="Social link"></div>
  <div class="social" style="left:845px" aria-label="Social link"></div>
</footer>

</body>
</html>
```